Manufacturer's Representative Group needs a clean new Website

We represent and sell a number of suppliers that design and build products used in Biopharmaceutical manufacturing. Our sales region is in the central US. Our customer base is scientific / engineering based - so clean, we organized design with a focus on the products - easy and clear navigation is necessary. We do not sell direct or warehouse product - so e-commerce is not needed. Our customers will use the website for reference on what we do and offer - we will use the site as a platform to present products from each vendor and the home page will be used to capture an overview and draw users deeper into the site. You can view our current site - which needs A LOT of help to get ideas on products represented and types of products

Target Market(s)

Engineers and Pharmaceutical / Bio pharm end users

Industry/Entity Type

E-Commerce

Number of Pages Required

2 page

Font styles to use
Sans Serif

Requirements
Must have
• I need a home page that provides a snapshot of my company and the product lines we represent - then a second page that I can copy as a template for each line I rep as well as for an "About us / contact" page.
• I would like to be able to manage content on the pages so something easy to adjust pictures or add content is a must
• Must use our logo

```html
<!DOCTYPE html>
<html lang="en">
<head>
<meta charset="utf-8">
<title>Northfield Biosolutions</title>
<link href="https://fonts.googleapis.com/css2?family=Open+Sans:wght@400;600;700&display=swap" rel="stylesheet">
<style>
:root{
  --orange:#e8661c;
  --navy:#0f1f6e;
  --text:#444;
  --muted:#808080;
  --line:#dcdcdc;
  --panel:#ececec;
  --footer-top:#4a4a4a;
  --footer-bottom:#2f2f2f;
  --footer-bar:#242424;
  --footer-text:#b8b8b8;
}
*{box-sizing:border-box;margin:0;padding:0}
html,body{width:785px;height:1200px;overflow:hidden;background:#fff}
body{font-family:"Open Sans",Arial,sans-serif;color:var(--text);position:relative}
.page{position:relative;width:785px;height:1200px}

/* header */
.brand{position:absolute;left:80px;top:24px;display:flex;align-items:center;gap:8px}
.brand-dot{width:18px;height:18px;border-radius:50%;background:var(--navy)}
.brand-name{font-size:24px;font-weight:600;color:var(--navy);letter-spacing:-.3px}
.main-nav{position:absolute;top:31px;left:348px;display:flex;align-items:center;font-size:8.5px;letter-spacing:.2px}
.main-nav a{color:#555;text-decoration:none;margin-right:25px}
.main-nav a.active{color:var(--orange)}
.btn-login,.btn-register{position:absolute;top:30px;height:21px;line-height:21px;padding:0 7px;font-size:8.5px;color:#fff;border-radius:2px}
.btn-login{left:606px;background:var(--navy)}
.btn-register{left:653px;background:var(--orange)}

/* hero */
.hero{position:absolute;left:77px;top:77px;width:631px;height:251px;background:linear-gradient(100deg,#e9eef2 0%,#f5f7f8 45%,#dde4e8 100%);overflow:hidden}
.hero-media{position:absolute;left:345px;top:55px;width:205px;height:185px;border-radius:6px;background:linear-gradient(135deg,#c3e75a 0%,#a9c94a 50%,#b9bcbf 100%)}
.hero-title{position:absolute;left:80px;top:74px;font-size:22px;font-weight:700;color:var(--navy)}
.hero-text{position:absolute;left:81px;top:106px;width:225px;font-size:9.5px;line-height:15px;color:#555}
.hero-btn{position:absolute;left:81px;top:158px;background:#8c8c8c;color:#fff;font-size:8.5px;font-weight:600;padding:5px 8px;border-radius:2px}
.hero-arrow{position:absolute;top:116px}
.hero-arrow.prev{left:13px}
.hero-arrow.next{right:13px}

/* partners */
.partners{position:absolute;left:77px;top:340px;width:631px;height:42px;display:flex;justify-content:space-between;align-items:center;font-size:13px;font-weight:600;color:#5a6a7a}
.partners span{white-space:nowrap}
.rule{position:absolute;left:77px;width:631px;height:1px;background:var(--line)}

/* welcome */
.welcome-title{position:absolute;left:0;width:785px;top:420px;text-align:center;font-size:20px;color:var(--orange);font-weight:400}
.welcome-text{position:absolute;left:108px;width:569px;top:452px;text-align:center;font-size:9px;line-height:16px;color:var(--muted)}

/* card rows */
.section-title{position:absolute;font-size:14.5px;font-weight:700;color:var(--navy);letter-spacing:.2px}
.pager{position:absolute;display:flex;gap:9px}
.cards{position:absolute;left:85px;display:flex;gap:8px}
.card{width:148px;height:148px;border:1px solid var(--line);background:#fff;padding:4px}
.card-media{width:140px;height:86px}
.card-text{font-size:8.8px;line-height:12px;color:#333;padding:8px 4px 0}
.card-date{font-size:8.5px;color:var(--muted);padding:5px 4px 0}
.updates{position:absolute;left:77px;top:770px;width:631px;height:204px;background:var(--panel)}

/* footer */
.footer{position:absolute;left:0;top:996px;width:785px;height:164px;background:linear-gradient(180deg,var(--footer-top),var(--footer-bottom))}
.footer h4{position:absolute;top:22px;font-size:9.5px;font-weight:400;color:#fff}
.footer ul{position:absolute;top:44px;list-style:none;font-size:7.8px;line-height:16px;color:var(--footer-text)}
.contact-field{position:absolute;left:506px;width:149px;border:1px solid #555;background:#353535;font-size:7.8px;color:#888;padding:6px 8px}
.submit{position:absolute;left:660px;top:123px;background:#5c5c5c;color:#eee;font-size:7.8px;padding:5px 7px;border-radius:2px}
.social{position:absolute;left:85px;top:124px;display:flex;gap:4px}
.social span{width:18px;height:18px;border-radius:2px;background:#9a9a9a}
.copyright{position:absolute;left:0;top:1160px;width:785px;height:40px;background:var(--footer-bar);text-align:center;line-height:40px;font-size:7.8px;color:#999}
</style>
</head>
<body>
<div class="page">

  <header>
    <div class="brand"><span class="brand-dot"></span><span class="brand-name">Northfield Bio</span></div>
    <nav class="main-nav">
      <a class="active" href="#">HOME</a><a href="#">ABOUT US</a><a href="#">PRODUCTS</a><a href="#">CONTACT US</a>
    </nav>
    <span class="btn-login">LOGIN</span>
    <span class="btn-register">REGISTER</span>
  </header>

  <section class="hero">
    <div class="hero-media" role="img" aria-label="Green bioreactor skid with stainless vessel and control panel"></div>
    <h1 class="hero-title">Aliquam nunc</h1>
    <p class="hero-text">Pellentesque posuere, neque auctor scelerisque dapibus, justo justo lacinia urna, non imperdiet quam tortor sit amet velit.</p>
    <span class="hero-btn">Read more</span>
    <svg class="hero-arrow prev" width="10" height="18" viewBox="0 0 10 18"><path d="M8 2 2 9l6 7" fill="none" stroke="#999" stroke-width="1.5"/></svg>
    <svg class="hero-arrow next" width="10" height="18" viewBox="0 0 10 18"><path d="M2 2l6 7-6 7" fill="none" stroke="#999" stroke-width="1.5"/></svg>
  </section>

  <div class="partners">
    <span>PureLine</span><span>Verant Polymers</span><span>Halden Pumps</span><span>Corvel</span><span>Flexa Tubing Co.</span><span>Modura Systems</span>
  </div>
  <div class="rule" style="top:396px"></div>

  <h2 class="welcome-title">Welcome to Northfield Biosolutions</h2>
  <p class="welcome-text">Northfield Biosolutions is a distribution channel, licensed partner and manufacturers representative group providing high quality fluid handling products and technical services to the Midwestern biopharmaceutical community. With a core staff of experienced professionals and a team approach to all customer needs, we offer over 30 years of cGMP experience in the selection and use of most process consumable products. We're looking forward to working with you!</p>
  <div class="rule" style="top:544px"></div>

  <h3 class="section-title" style="left:86px;top:572px">NEWEST STORIES</h3>
  <div class="pager" style="left:671px;top:577px">
    <svg width="6" height="9" viewBox="0 0 6 9"><path d="M5 1 1 4.5 5 8" fill="none" stroke="#555" stroke-width="1.6"/></svg>
    <svg width="6" height="9" viewBox="0 0 6 9"><path d="M1 1l4 3.5L1 8" fill="none" stroke="#555" stroke-width="1.6"/></svg>
  </div>
  <div class="cards" style="top:599px">
    <div class="card"><div class="card-media" role="img" aria-label="Coiled clear tubing on blue background" style="background:linear-gradient(135deg,#0c2a6e,#3a6fc2)"></div><p class="card-text">Morbi venenatis vestibu lum quam, eu commodo leo.</p><p class="card-date">Dec 23, 2014</p></div>
    <div class="card"><div class="card-media" role="img" aria-label="Modular cleanroom units" style="background:linear-gradient(180deg,#e4e6e6,#bfc3c2)"></div><p class="card-text">Morbi venenatis vestibu lum quam, eu commodo leo.</p><p class="card-date">Dec 23, 2014</p></div>
    <div class="card"><div class="card-media" role="img" aria-label="Red peristaltic pump with display" style="background:linear-gradient(135deg,#b8202a,#d9d3c4)"></div><p class="card-text">Morbi venenatis vestibu lum quam, eu commodo leo.</p><p class="card-date">Dec 23, 2014</p></div>
    <div class="card"><div class="card-media" role="img" aria-label="Silicone fittings and gaskets" style="background:linear-gradient(135deg,#1f3e78,#8fa6c7)"></div><p class="card-text">Morbi venenatis vestibu lum quam, eu commodo leo.</p><p class="card-date">Dec 23, 2014</p></div>
  </div>

  <section class="updates"></section>
  <h3 class="section-title" style="left:87px;top:783px">LATEST UPDATES</h3>
  <div class="pager" style="left:671px;top:789px">
    <svg width="6" height="9" viewBox="0 0 6 9"><path d="M5 1 1 4.5 5 8" fill="none" stroke="#555" stroke-width="1.6"/></svg>
    <svg width="6" height="9" viewBox="0 0 6 9"><path d="M1 1l4 3.5L1 8" fill="none" stroke="#555" stroke-width="1.6"/></svg>
  </div>
  <div class="cards" style="top:810px">
    <div class="card"><div class="card-media" role="img" aria-label="Clear media bottles with tubing" style="background:linear-gradient(180deg,#9a9a9a,#d8dbe6)"></div><p class="card-text">Morbi venenatis vestibu lum quam, eu commodo leo.</p><p class="card-date">Dec 23, 2014</p></div>
    <div class="card"><div class="card-media" role="img" aria-label="Close-up of a labelled container base" style="background:linear-gradient(180deg,#7e7c6a,#c4c2a6)"></div><p class="card-text">Morbi venenatis vestibu lum quam, eu commodo leo.</p><p class="card-date">Dec 23, 2014</p></div>
    <div class="card"><div class="card-media" role="img" aria-label="Single-use bioprocess bags" style="background:linear-gradient(135deg,#cfe6f2,#f4f9fb)"></div><p class="card-text">Morbi venenatis vestibu lum quam, eu commodo leo.</p><p class="card-date">Dec 23, 2014</p></div>
    <div class="card"><div class="card-media" role="img" aria-label="Bag containers and transport carts" style="background:linear-gradient(135deg,#e9c6c8,#cfe3ee)"></div><p class="card-text">Morbi venenatis vestibu lum quam, eu commodo leo.</p><p class="card-date">Dec 23, 2014</p></div>
  </div>

  <footer class="footer">
    <h4 style="left:85px">Navigation Menu</h4>
    <ul style="left:85px"><li>Home</li><li>About us</li><li>Products</li><li>Contact us</li></ul>
    <ul style="left:152px"><li>Register</li><li>Login</li></ul>
    <h4 style="left:252px">Support Links</h4>
    <ul style="left:252px"><li>Privacy Policy</li><li>Terms and Conditions</li><li>Customer Support</li><li>FAQ</li></ul>
    <h4 style="left:400px">About us</h4>
    <ul style="left:400px"><li>Who we are</li><li>What we do</li><li>Our Projects</li><li>Our History</li></ul>
    <h4 style="left:508px">Contact us</h4>
    <div class="contact-field" style="top:48px;height:23px">Name</div>
    <div class="contact-field" style="top:75px;height:23px">E-mail</div>
    <div class="contact-field" style="top:102px;height:43px">Comment</div>
    <span class="submit">SUBMIT</span>
    <div class="social" aria-label="Social links"><span></span><span></span><span></span><span></span><span></span></div>
  </footer>
  <div class="copyright">Copyright © 2014 Northfield Biosolutions. &nbsp; All rights reserved.</div>

</div>
</body>
</html>
```